Packaging label design for Crystal water bottles

Hello, I am new to plotquarry and I am needing to have my packaging label designed for the crystal water bottles I'm manufacturing. The product name is Velumo Morrow Tide, the company is PELLVOT. The packaging is tube shaped cardboard like container, similar to what scotch bottles come in. I have included the diecut and the sample box that the manufacturer sent to me. Also included a photo of a concept idea and any logos or photos you may need.The font that is used for my logo is Pristina, if that can be used for everything but PELLVOT. (I used Proxima Nova for that)I would like the information on it to be: (and again this is just a concept I am open to adjustments and change) Morrow Tide- on the lid sectionAkasha by PELLVOT (I'm thinking that I might want this one a bit smaller and off set like a signature)500mlHighland, UT 84003www.akashacrystalenergy.comAnd have sacred geometry art on it such as Metatrons Cube, Fibonacci Spiral, or any other sacred geometry that might be appropriate or fitting.Again I am open to other options if you feel like you have a great idea for something different. Also i'm not sure if all the photos uploaded correctly, so let me know if one of them didn't work. Thank you.

```html
<!DOCTYPE html>
<html lang="en">
<head>
<meta charset="utf-8">
<title>Velumo Morrow Tide – Tube Label Dieline</title>
<link rel="stylesheet" href="https://fonts.googleapis.com/css2?family=Kaushan+Script&family=Open+Sans:wght@300;400&display=swap">
<style>
  :root {
    --paper: #ffffff;
    --dim-blue: #1fa3dd;
    --cream: #fcd888;
    --sand: #d4ae6e;
    --bronze: #a98240;
    --pale-gold: #f8d98e;
    --ink: #1a1410;
    --edge: #3a2c18;
    --geo-light: rgba(255, 246, 214, 0.55);
    --geo-band: rgba(232, 200, 140, 0.35);
  }
  html, body {
    margin: 0;
    padding: 0;
    overflow: hidden;
    background: var(--paper);
  }
  .sheet {
    position: relative;
    width: 885px;
    height: 1200px;
    overflow: hidden;
    background: var(--paper);
    font-family: "Open Sans", sans-serif;
  }
  .dim-label {
    position: absolute;
    color: var(--dim-blue);
    font-size: 17px;
    font-family: "Open Sans", sans-serif;
    white-space: nowrap;
  }
  .dim-label--diameter { left: 354px; top: 50px; }
  .dim-label--cap-top { left: 31px; top: 402px; }
  .dim-label--cap-bottom { left: 31px; top: 1102px; }
  .dim-label--vertical {
    transform: translate(-50%, -50%) rotate(90deg);
  }
  .dim-label--lid-height { left: 812px; top: 503px; }
  .dim-label--body-height { left: 822px; top: 968px; }
  .dim-label--width { left: 449px; top: 1148px; transform: translateX(-50%); }

  .dimension-lines {
    position: absolute;
    left: 0; top: 0;
    width: 885px; height: 1200px;
    pointer-events: none;
  }

  .end-disc {
    position: absolute;
    border-radius: 50%;
    border: 1px solid var(--edge);
    display: flex;
    align-items: center;
    justify-content: center;
    box-sizing: border-box;
  }
  .end-disc--mark {
    left: 133px; top: 125px;
    width: 188px; height: 188px;
    background: var(--cream);
  }
  .end-disc--name {
    left: 472px; top: 124px;
    width: 194px; height: 194px;
    background: var(--sand);
  }
  .disc-wordmark {
    font-family: "Kaushan Script", cursive;
    color: var(--ink);
    font-size: 30px;
    text-align: center;
    line-height: 1.15;
  }
  .disc-wordmark--brand {
    font-family: "Open Sans", sans-serif;
    font-weight: 400;
    font-size: 24px;
    letter-spacing: 1px;
  }

  .label {
    position: absolute;
    left: 107px;
    top: 400px;
    width: 684px;
  }
  .label__cap-strip {
    height: 29px;
    background: var(--sand);
    border: 1px solid var(--edge);
    border-bottom: none;
    box-sizing: border-box;
  }
  .label__lid {
    position: relative;
    height: 147px;
    background: var(--bronze);
    border: 1px solid var(--edge);
    box-sizing: border-box;
    overflow: hidden;
  }
  .label__lid-geometry {
    position: absolute;
    left: 211px; top: -39px;
    width: 260px; height: 260px;
    border-radius: 50%;
    background: radial-gradient(circle, var(--geo-band) 0%, rgba(232,200,140,0.12) 70%, transparent 72%);
  }
  .label__lid-title {
    position: absolute;
    left: 0; right: 0;
    top: 36px;
    text-align: center;
    font-family: "Kaushan Script", cursive;
    font-size: 60px;
    color: var(--pale-gold);
    line-height: 1;
  }
  .label__body {
    position: relative;
    height: 523px;
    background: var(--cream);
    border: 1px solid var(--edge);
    border-top: none;
    box-sizing: border-box;
    overflow: hidden;
  }
  .label__geometry {
    position: absolute;
    border-radius: 50%;
    background: radial-gradient(circle, var(--geo-light) 0%, rgba(255,246,214,0.25) 68%, transparent 71%);
  }
  .geo--left-large { left: 13px; top: 61px; width: 208px; height: 208px; }
  .geo--right-top { left: 510px; top: 54px; width: 124px; height: 124px; }
  .geo--right-small { left: 419px; top: 141px; width: 98px; height: 98px; }
  .geo--right-large { left: 437px; top: 228px; width: 234px; height: 234px; }
  .geo--left-small { left: 168px; top: 275px; width: 96px; height: 96px; }
  .geo--left-bottom { left: 31px; top: 332px; width: 140px; height: 140px; }

  .product-name {
    position: absolute;
    left: 302px; top: 174px;
    transform: translate(-50%, -50%) rotate(-90deg);
    font-family: "Kaushan Script", cursive;
    font-size: 104px;
    color: var(--ink);
    line-height: 1;
    white-space: nowrap;
  }
  .product-maker {
    position: absolute;
    left: 403px; top: 153px;
    transform: translate(-50%, -50%) rotate(-90deg);
    font-family: "Open Sans", sans-serif;
    font-weight: 400;
    font-size: 24px;
    color: var(--ink);
    white-space: nowrap;
  }
  .product-details {
    position: absolute;
    left: 0; right: 0;
    top: 446px;
    text-align: center;
    font-family: "Open Sans", sans-serif;
    font-size: 16px;
    line-height: 21px;
    color: var(--ink);
    letter-spacing: 0.5px;
  }
  .product-details p { margin: 0; }
  .label__base-strip {
    height: 31px;
    background: var(--bronze);
    border: 1px solid var(--edge);
    border-top: none;
    box-sizing: border-box;
  }
</style>
</head>
<body>
<main class="sheet">
  <span class="dim-label dim-label--diameter">D:Φ83mm</span>

  <div class="end-disc end-disc--mark">
    <span class="disc-wordmark disc-wordmark--brand">PELLVOT</span>
  </div>
  <div class="end-disc end-disc--name">
    <span class="disc-wordmark">Velumo<br><span style="font-size:20px">Morrow Tide</span></span>
  </div>

  <span class="dim-label dim-label--cap-top">12mm</span>
  <span class="dim-label dim-label--cap-bottom">12mm</span>
  <span class="dim-label dim-label--vertical dim-label--lid-height">H:60mm</span>
  <span class="dim-label dim-label--vertical dim-label--body-height">H:215mm</span>
  <span class="dim-label dim-label--width">W:280mm</span>

  <svg class="dimension-lines" viewBox="0 0 885 1200" aria-hidden="true">
    <g stroke="#1fa3dd" stroke-width="1" fill="none">
      <line x1="796" y1="429" x2="796" y2="1099"/>
      <line x1="791" y1="429" x2="801" y2="429"/>
      <line x1="791" y1="576" x2="826" y2="576"/>
      <line x1="791" y1="1099" x2="826" y2="1099"/>
      <line x1="107" y1="1142" x2="791" y2="1142"/>
      <line x1="107" y1="1134" x2="107" y2="1150"/>
      <line x1="791" y1="1134" x2="791" y2="1150"/>
    </g>
  </svg>

  <section class="label">
    <div class="label__cap-strip"></div>
    <div class="label__lid">
      <div class="label__lid-geometry" role="img" aria-label="Faint sacred geometry circle behind the lid title"></div>
      <h1 class="label__lid-title" style="margin:0;font-weight:400">Morrow Tide</h1>
    </div>
    <div class="label__body">
      <div class="label__geometry geo--left-large" role="img" aria-label="Sacred geometry Metatron's cube pattern"></div>
      <div class="label__geometry geo--right-top" role="img" aria-label="Sacred geometry Metatron's cube pattern"></div>
      <div class="label__geometry geo--right-small" role="img" aria-label="Sacred geometry Metatron's cube pattern"></div>
      <div class="label__geometry geo--right-large" role="img" aria-label="Sacred geometry Metatron's cube pattern"></div>
      <div class="label__geometry geo--left-small" role="img" aria-label="Sacred geometry Metatron's cube pattern"></div>
      <div class="label__geometry geo--left-bottom" role="img" aria-label="Sacred geometry Metatron's cube pattern"></div>

      <span class="product-name">Velumo</span>
      <span class="product-maker">By PELLVOT</span>

      <div class="product-details">
        <p>500ml</p>
        <p>Fernhollow UT 84077</p>
        <p>www.velumomorrowtide.com</p>
      </div>
    </div>
    <div class="label__base-strip"></div>
  </section>
</main>
</body>
</html>
```